Spiritual Healing bussiness needs logo/business card

Simple, clean looking logo/card
For spiritual business with healing services and occult rituals

Contact Information for Business Card

Needs my name: Tobin Varley
Business name: Lantern Healing Shop
Services provided and worded in this way:

Reiki Healing
Tarot
Oils
Rituals Of Change

Can look occult like but with light energy.

Colors
0255a3
3276b5
85abd2
33a6d7
85cae6
0292cd

```html
<!DOCTYPE html>
<html lang="en">
<head>
<meta charset="utf-8">
<title>Lantern Healing Shop – Business Card</title>
<link href="https://fonts.googleapis.com/css2?family=Oswald:wght@500&family=Roboto:wght@400&family=Lato:wght@400&display=swap" rel="stylesheet">
<style>
  :root {
    --navy: #0255a3;
    --mid-blue: #3276b5;
    --sky: #0292cd;
    --bright: #33a6d7;
    --pale: #85cae6;
    --ink: #1a1a1a;
    --grey-text: #555555;
    --rule: #8a8a8a;
    --backdrop: #2f2f2f;
    --white: #ffffff;
  }
  html, body {
    margin: 0;
    width: 1200px;
    height: 1200px;
    overflow: hidden;
    background: var(--backdrop);
  }
  .canvas {
    position: relative;
    width: 1200px;
    height: 1200px;
  }
  .card {
    position: absolute;
    top: 310px;
    height: 594px;
    box-shadow: 0 4px 10px rgba(0,0,0,.45);
  }
  .card-front {
    left: 234px;
    width: 364px;
    background: var(--white);
    text-align: center;
  }
  .card-back {
    left: 627px;
    width: 369px;
    background: var(--navy);
    text-align: center;
  }
  .brand-dot {
    position: absolute;
    left: 112px;
    top: 90px;
    width: 140px;
    height: 140px;
    border-radius: 50%;
    background: var(--sky);
  }
  .brand-name {
    position: absolute;
    left: 0;
    width: 100%;
    top: 248px;
    margin: 0;
    font-family: "Oswald", sans-serif;
    font-weight: 500;
    font-size: 36px;
    line-height: 1;
    color: var(--navy);
    letter-spacing: 0.2px;
  }
  .tagline {
    position: absolute;
    left: 0;
    width: 100%;
    top: 296px;
    margin: 0;
    font-family: "Roboto", sans-serif;
    font-size: 14.5px;
    color: var(--grey-text);
    letter-spacing: 0.3px;
  }
  .person-name {
    position: absolute;
    left: 0;
    width: 100%;
    top: 396px;
    margin: 0;
    font-family: "Oswald", sans-serif;
    font-weight: 500;
    font-size: 28px;
    line-height: 1;
    color: var(--navy);
  }
  .contact-icons {
    position: absolute;
    left: 86px;
    top: 447px;
  }
  .contact-list {
    position: absolute;
    left: 0;
    width: 100%;
    top: 484px;
    margin: 0;
    padding: 0;
    list-style: none;
    font-family: "Lato", sans-serif;
    font-size: 17px;
    line-height: 22px;
    color: var(--ink);
  }
  .back-disc {
    position: absolute;
    left: 40px;
    top: 100px;
    width: 289px;
    height: 289px;
    border-radius: 50%;
    background: var(--sky);
  }
  .back-name {
    position: absolute;
    left: 0;
    width: 100%;
    top: 410px;
    margin: 0;
    font-family: "Oswald", sans-serif;
    font-weight: 500;
    font-size: 32px;
    line-height: 1;
    color: var(--white);
  }
  .services {
    position: absolute;
    left: 0;
    width: 100%;
    top: 503px;
    margin: 0;
    font-family: "Lato", sans-serif;
    font-size: 18.5px;
    line-height: 27px;
    color: var(--white);
  }
  .services .sep {
    display: inline-block;
    width: 8px;
    height: 8px;
    border-radius: 50%;
    background: var(--white);
    margin: 0 10px;
    vertical-align: middle;
  }
</style>
</head>
<body>
<main class="canvas">
  <section class="card card-front">
    <div class="brand-dot"></div>
    <h1 class="brand-name">LANTERN HEALING SHOP</h1>
    <p class="tagline">HEALING SERVICES &amp; OCCULT RITUALS</p>
    <h2 class="person-name">TOBIN VARLEY</h2>
    <svg class="contact-icons" width="192" height="28" viewBox="0 0 192 28" aria-hidden="true">
      <line x1="0" y1="14" x2="54" y2="14" stroke="var(--rule)" stroke-width="1"/>
      <line x1="138" y1="14" x2="192" y2="14" stroke="var(--rule)" stroke-width="1"/>
      <circle cx="68" cy="14" r="12" fill="var(--navy)"/>
      <circle cx="96" cy="14" r="12" fill="var(--navy)"/>
      <circle cx="124" cy="14" r="12" fill="var(--navy)"/>
      <!-- phone -->
      <path d="M62 11 q6 -4 12 0 v2 h-3 v-1.5 q-3 -1 -6 0 v1.5 h-3z M63 15 h10 v4 h-10z" fill="var(--white)"/>
      <!-- envelope -->
      <rect x="90" y="10" width="12" height="8" fill="none" stroke="var(--white)" stroke-width="1.4"/>
      <path d="M90 10 l6 5 l6 -5" fill="none" stroke="var(--white)" stroke-width="1.4"/>
      <!-- globe -->
      <circle cx="124" cy="14" r="6" fill="none" stroke="var(--white)" stroke-width="1.4"/>
      <ellipse cx="124" cy="14" rx="2.5" ry="6" fill="none" stroke="var(--white)" stroke-width="1"/>
      <line x1="118" y1="14" x2="130" y2="14" stroke="var(--white)" stroke-width="1"/>
    </svg>
    <ul class="contact-list">
      <li>044-987 654 321</li>
      <li>info@lanternhealing.com</li>
      <li>www.LanternHealingShop.com</li>
    </ul>
  </section>

  <section class="card card-back">
    <div class="back-disc"></div>
    <p class="back-name">LANTERN HEALING SHOP</p>
    <p class="services">
      REIKI HEALING<span class="sep"></span>TAROT<br>
      OILS<span class="sep"></span>RITUALS OF CHANGE
    </p>
  </section>
</main>
</body>
</html>
```